life insurance quote website design for lepontdoriole.ca

the web site lepontdoriole.ca need a design. we dont like the actuel one but we are open at all new suggestion. visit us at lepontdoriole.ca and you will understand. the principal concurant is tarifsgarantisnord.ca, calculeo.ca, coutprotecfam.ca. We are a life insurance quote site. we found best price available in the canadien industrie. We absolutly want a design with our form in the front page on the top right side like our concurance, we use wordpress at this time. we want to be able to switch language. and to have a logic form. we want to be able to change the color for each type of insurance quote page.we also need a blog in it to post news. and the site will be SEO accurate.

Target Market(s)

Get client fill the quote form

Industry/Entity Type

Insurance

Number of Pages Required

3 page

Font styles to use
Sans Serif

Requirements
Must have
• logic form on the top right first page
• page template for product info stuff, contact, and who we are, blog
• French site
• custum color
Nice to have
• Wordpress design will be appréciate
• switch language english/french

```html
<!DOCTYPE html>
<html lang="en">
<head>
<meta charset="utf-8">
<title>lepontdoriole.ca — Life Insurance Quotes</title>
<link href="https://fonts.googleapis.com/css2?family=Open+Sans:wght@400;600;700;800&display=swap" rel="stylesheet">
<style>
:root{
  --blue:#1b7fd0;
  --blue-dark:#0f5fa6;
  --navy:#0d4f8f;
  --red:#d42a2a;
  --red-dark:#b61f1f;
  --ink:#2b2b2b;
  --muted:#6a6a6a;
  --line:#e2e2e2;
  --gray-bg:#f2f4f6;
  --white:#ffffff;
  --teal:#2eb3d9;
  --gold:#d9a040;
  --green:#5cb85c;
  --pink:#ec5f86;
}
*{box-sizing:border-box;margin:0;padding:0}
html,body{width:1200px;height:2761px;overflow:hidden}
body{font-family:"Open Sans",Arial,sans-serif;color:var(--ink);background:var(--white);position:relative}
.abs{position:absolute}

/* top bar */
.topbar{left:0;top:0;width:1200px;height:86px;background:var(--white)}
.topbar .contact-item{top:26px;display:flex;align-items:center;gap:10px;font-size:13px;color:var(--ink)}
.circle-icon{width:26px;height:26px;border:1.5px solid var(--blue);border-radius:50%;display:flex;align-items:center;justify-content:center}
.lang-select{left:847px;top:26px;width:124px;height:34px;border:1px solid #d5d5d5;border-radius:3px;display:flex;align-items:center;font-size:10px;color:#777;padding-left:8px;gap:8px}
.lang-select .flag{width:18px;height:12px;background:#2a4a8c;border-radius:1px}
.lang-select .caret{margin-left:auto;width:24px;height:100%;border-left:1px solid #d5d5d5;display:flex;align-items:center;justify-content:center}
.login-btn{left:978px;top:26px;width:124px;height:34px;background:var(--blue);border-radius:3px;color:#fff;font-size:12px;font-weight:600;display:flex;align-items:center;justify-content:center;gap:8px}

/* nav */
.mainnav{left:0;top:86px;width:1200px;height:56px;background:linear-gradient(#2e93e0,#1672c2)}
.mainnav a{position:absolute;top:0;height:56px;line-height:56px;color:#fff;font-size:11px;font-weight:600;text-decoration:none;text-align:center;text-transform:uppercase}
.mainnav a.active{background:var(--red)}
.nav-search{left:1003px;top:0;width:97px;height:56px;background:var(--blue-dark);display:flex;align-items:center;justify-content:center}

.brand{left:534px;top:22px;width:132px;height:160px;background:var(--white);border-radius:14px;box-shadow:0 4px 12px rgba(0,0,0,.25);display:flex;flex-direction:column;align-items:center;justify-content:center;gap:12px;z-index:5}
.brand .dot{width:40px;height:40px;border-radius:50%;background:var(--red)}
.brand .name{font-size:14px;font-weight:700;color:var(--red)}

/* hero */
.hero{left:0;top:142px;width:1200px;height:511px;background:linear-gradient(180deg,#8ec2ea 0%,#b9d9ef 35%,#9cc46a 70%,#5e9a32 100%)}
.hero-caption{left:114px;top:482px;width:420px;height:61px;background:rgba(255,255,255,.35);color:var(--red);font-size:30px;font-weight:700;line-height:61px;padding-left:10px}
.hero-arrows{left:98px;top:560px;display:flex;gap:6px}

/* quote form */
.quote{left:810px;top:230px;width:290px;height:666px;background:var(--white);box-shadow:0 3px 14px rgba(0,0,0,.22);border-radius:3px}
.quote-head{height:46px;background:linear-gradient(#2e93e0,#1672c2);color:#fff;font-size:20px;font-weight:600;text-align:center;line-height:46px;border-radius:3px 3px 0 0}
.quote-body{padding:14px 24px 0}
.form-label{font-size:11px;font-weight:700;margin:8px 0 10px}
.field{height:32px;border:1px solid var(--line);border-radius:2px;font-size:10px;color:#777;display:flex;align-items:center;padding-left:10px;margin-bottom:10px}
.field.select::after{content:"";margin-left:auto;margin-right:12px;width:5px;height:5px;border-right:1.5px solid #777;border-bottom:1.5px solid #777;transform:rotate(45deg)}
.check{display:flex;gap:8px;font-size:9.5px;color:#555;margin-bottom:10px;align-items:flex-start;line-height:1.4}
.check .box{flex:none;width:13px;height:13px;border:1px solid #bbb}
.captcha{height:44px;border:1px solid var(--line);margin:6px 0 14px;display:flex;align-items:center;justify-content:center;font-size:22px;color:#333;letter-spacing:2px;font-weight:600}
.send-btn{height:38px;background:var(--red);border-radius:3px;color:#fff;font-size:11px;font-weight:700;text-align:center;line-height:38px}

/* intro */
.intro{left:98px;top:690px;width:680px}
.section-title{color:var(--blue);font-size:22px;font-weight:700;text-transform:uppercase}
.intro p{font-size:11px;line-height:23px;color:#555;margin-top:18px}

/* features */
.features{left:0;top:951px;width:1200px;height:457px;background:var(--gray-bg)}
.center-title{width:1200px;text-align:center}
.feature-card{top:1054px;width:234px;height:298px;background:var(--white);border:1px solid var(--line);text-align:center;padding-top:26px}
.feature-card .ico{width:80px;height:80px;border-radius:50%;margin:0 auto;display:flex;align-items:center;justify-content:center;border:3px solid #fff;box-shadow:0 0 0 2px #ddd}
.feature-card h3{font-size:13px;font-weight:700;margin-top:26px;text-transform:uppercase}
.feature-card p{font-size:10px;line-height:22px;color:#666;padding:8px 22px 0}
.feature-card .more{display:inline-block;margin-top:10px;font-size:11px;font-weight:700;text-decoration:underline}
.feature-card .bar{position:absolute;left:0;bottom:-1px;width:100%;height:3px}

/* best price */
.best-copy{left:110px;top:1492px;width:980px;text-align:center;font-size:10.5px;line-height:24px;color:#555}
.tags{left:98px;top:1646px;width:1004px;display:flex;justify-content:space-between;font-size:10px;color:#444;text-transform:uppercase}
.tags span{display:flex;align-items:center;gap:9px}
.tags i{width:16px;height:16px;border-radius:50%;background:var(--red);display:flex;align-items:center;justify-content:center}
.article{top:1704px;width:311px;text-align:center}
.article .photo{height:198px;box-shadow:0 2px 6px rgba(0,0,0,.25)}
.article h4{font-size:13px;font-weight:700;margin-top:28px}
.article p{font-size:10.5px;line-height:22px;color:#666;margin-top:8px;padding:0 16px}
.red-btn{display:inline-block;margin-top:16px;width:114px;height:37px;background:var(--red);color:#fff;font-size:11px;font-weight:700;line-height:37px;border-radius:2px}

/* blog */
.blog{left:0;top:2101px;width:1200px;height:341px;background:linear-gradient(#1960a6,#0f4e8e);border-top:4px solid var(--red)}
.blog-title{top:2141px;color:#fff;font-size:22px;font-weight:700}
.blog-sub{top:2180px;color:#e7eef7;font-size:13px}
.view-all{left:1054px;top:2152px;color:#fff;font-size:10px;font-weight:600}
.post{top:2226px;width:487px;height:166px;background:var(--white);display:flex}
.post .photo{width:200px;height:100%;flex:none}
.post .body{padding:20px 22px}
.post h5{font-size:13px;font-weight:600;line-height:20px}
.post .date{font-size:10px;color:var(--red);font-weight:700;margin-top:8px}
.post p{font-size:10.5px;line-height:20px;color:#666;margin-top:8px}

/* footer */
.footer{left:0;top:2442px;width:1200px;height:263px;background:var(--gray-bg)}
.foot-col{top:2477px}
.foot-col h6{font-size:13px;font-weight:700;text-transform:uppercase;margin-bottom:18px}
.foot-col li{list-style:none;font-size:10.5px;line-height:26px;color:#555}
.hours td{font-size:10.5px;line-height:26px;color:#555;padding-right:8px}
.hours tr.sat td{color:var(--red)}
.offices{display:grid;grid-template-columns:92px 88px 80px;font-size:10.5px;line-height:26px;color:#555}
.contact-line{display:flex;align-items:center;gap:10px;font-size:10.5px;line-height:26px;color:#555;white-space:nowrap}
.socials{display:flex;gap:8px;margin-top:16px}
.socials span{width:26px;height:26px;border-radius:50%}
.copyright{left:0;top:2705px;width:1200px;height:56px;background:var(--gray-bg);border-top:1px solid #dcdcdc;text-align:center;font-size:10px;font-weight:600;color:#444;line-height:56px}
</style>
</head>
<body>

<!-- top bar -->
<div class="abs topbar">
  <div class="abs contact-item" style="left:98px">
    <span class="circle-icon"><svg width="12" height="12" viewBox="0 0 24 24"><path fill="#1b7fd0" d="M6.6 10.8a15 15 0 006.6 6.6l2.2-2.2c.3-.3.7-.4 1-.2 1.1.4 2.3.6 3.6.6.6 0 1 .4 1 1V20c0 .6-.4 1-1 1A17 17 0 013 4c0-.6.4-1 1-1h3.5c.6 0 1 .4 1 1 0 1.3.2 2.5.6 3.6.1.3 0 .7-.2 1z"/></svg></span>
    1-855-555-0142
  </div>
  <div class="abs contact-item" style="left:242px">
    <span class="circle-icon"><svg width="12" height="10" viewBox="0 0 24 18"><rect x="1" y="1" width="22" height="16" fill="none" stroke="#1b7fd0" stroke-width="2"/><path d="M1 1l11 9 11-9" fill="none" stroke="#1b7fd0" stroke-width="2"/></svg></span>
    contact@lepontdoriole.ca
  </div>
  <div class="abs lang-select"><span class="flag"></span>LANGUAGE<span class="caret"><svg width="8" height="6" viewBox="0 0 8 6"><path d="M0 0h8L4 6z" fill="#888"/></svg></span></div>
  <div class="abs login-btn"><svg width="10" height="12" viewBox="0 0 10 12"><rect x="0" y="5" width="10" height="7" rx="1" fill="#fff"/><path d="M2.5 5V3.5a2.5 2.5 0 015 0V5" stroke="#fff" stroke-width="1.5" fill="none"/></svg>LOG IN</div>
</div>

<!-- navigation -->
<nav class="abs mainnav">
  <a class="active" style="left:98px;width:128px">Home</a>
  <a style="left:226px;width:112px">Products</a>
  <a style="left:362px;width:112px">Submission</a>
  <a style="left:726px;width:112px">Who are we?</a>
  <a style="left:872px;width:112px">Contact us</a>
  <div class="abs nav-search"><svg width="16" height="16" viewBox="0 0 16 16"><circle cx="6.5" cy="6.5" r="5" stroke="#fff" stroke-width="2" fill="none"/><path d="M10.5 10.5L15 15" stroke="#fff" stroke-width="2"/></svg></div>
</nav>

<div class="abs brand"><span class="dot"></span><span class="name">lepontdoriole.ca</span></div>

<!-- hero -->
<div class="abs hero" role="img" aria-label="Photo of a smiling family lying on green grass in front of a house"></div>
<div class="abs hero-caption">FIND THE BEST INSURANCE</div>
<div class="abs hero-arrows">
  <svg width="14" height="36" viewBox="0 0 14 36"><path d="M12 2L2 18l10 16" stroke="#fff" stroke-width="2" fill="none"/></svg>
  <svg width="14" height="36" viewBox="0 0 14 36"><path d="M2 2l10 16L2 34" stroke="#fff" stroke-width="2" fill="none"/></svg>
</div>

<!-- quote form -->
<form class="abs quote">
  <div class="quote-head">Quote Request</div>
  <div class="quote-body">
    <div class="form-label">PRODUCT:</div>
    <div class="field select">Types of insurance</div>
    <div class="form-label">APPLICANT:</div>
    <div class="field">Full Name *</div>
    <div class="field select">Cities *</div>
    <div class="field">Email *</div>
    <div class="field">Phone *</div>
    <div class="field">Age *</div>
    <div class="field select">Gender *</div>
    <div class="form-label">APPLICANT:</div>
    <div class="check"><span class="box"></span>Add a co-Applicant</div>
    <div class="check"><span class="box"><svg width="11" height="11" viewBox="0 0 11 11"><path d="M2 5.5l2.5 2.5L9 2.5" stroke="#333" stroke-width="1.5" fill="none"/></svg></span>I HAVE READ AND ACCEPT THE USE AND PRIVACY POLICY OF **</div>
    <div class="captcha">just example</div>
    <div class="send-btn">CLICK HERE TO SEND!</div>
  </div>
</form>

<!-- how to proceed -->
<section class="abs intro">
  <h2 class="section-title">How to proceed?</h2>
  <p>Simply fill in the insurance quote online form above, clicking on the insurance category that fits your needs. As soon as we receive it, we will send your request to 21 different insurance companies to compare the prices offered. We have access to products of the most renowned insurers in the country - they hold 97% of the insurance supply in Canada.</p>
  <p>Once your application is submitted to insurers and options obtained, we will contact an independent financial security advisor who will help you find the coverage that best suits you. This allows you to quickly obtain prices from several insurers with ease confidentially and without obligation on your part...</p>
</section>

<!-- features -->
<section class="abs features"></section>
<h2 class="abs section-title center-title" style="left:0;top:996px">Features</h2>

<div class="abs feature-card" style="left:98px">
  <div class="ico" style="background:var(--teal)"><svg width="34" height="34" viewBox="0 0 34 34"><path d="M3 17a14 14 0 0128 0z" fill="#fff"/><path d="M17 17v10a3 3 0 01-6 0" stroke="#fff" stroke-width="2.5" fill="none"/></svg></div>
  <h3>Assurance more</h3>
  <p>It is a long established fact that a read will be distracted by the read it look ike readable English...</p>
  <span class="more" style="color:var(--teal)">READ MORE</span>
  <span class="bar" style="background:var(--teal)"></span>
</div>
<div class="abs feature-card" style="left:355px">
  <div class="ico" style="background:var(--gold)"><svg width="34" height="26" viewBox="0 0 34 26"><rect x="2" y="3" width="30" height="20" rx="2" fill="none" stroke="#fff" stroke-width="2.5"/><circle cx="17" cy="13" r="5" fill="#fff"/></svg></div>
  <h3>Salary</h3>
  <p>It is a long established fact that a read will be distracted by the read it look ike readable English...</p>
  <span class="more" style="color:var(--gold)">READ MORE</span>
  <span class="bar" style="background:var(--gold)"></span>
</div>
<div class="abs feature-card" style="left:611px">
  <div class="ico" style="background:var(--green)"><svg width="34" height="30" viewBox="0 0 34 30"><rect x="2" y="8" width="30" height="20" rx="2" fill="#fff"/><path d="M12 8V4h10v4" stroke="#fff" stroke-width="2.5" fill="none"/><path d="M2 16h30" stroke="#5cb85c" stroke-width="2"/></svg></div>
  <h3>Hypothecaire</h3>
  <p>It is a long established fact that a read will be distracted by the read it look ike readable English...</p>
  <span class="more" style="color:var(--green)">READ MORE</span>
  <span class="bar" style="background:var(--green)"></span>
</div>
<div class="abs feature-card" style="left:867px">
  <div class="ico" style="background:var(--pink)"><svg width="34" height="36" viewBox="0 0 34 36"><circle cx="17" cy="5" r="3" stroke="#fff" stroke-width="2.5" fill="none"/><path d="M17 8v25M10 13h14M4 22a13 11 0 0026 0" stroke="#fff" stroke-width="2.5" fill="none"/></svg></div>
  <h3>Maladies graves</h3>
  <p>It is a long established fact that a read will be distracted by the read it look ike readable English...</p>
  <span class="more" style="color:var(--pink)">READ MORE</span>
  <span class="bar" style="background:var(--pink)"></span>
</div>

<!-- best price -->
<h2 class="abs section-title center-title" style="left:0;top:1444px">Find the best insurance at the best price!</h2>
<div class="abs best-copy">
  Whether you are looking for life insurance, mortgage insurance or else you certainly want to pay the most advantageous price. Navigating among the many offers in the field of insurance can be a real headache. But thanks to the intervention of Financial Security Advisors of Le Pont d'Oriole, will save you hours of fruitless search, and in addition, you will find an insurance policy that suits you, at a price that fully meets the constraints on your<br><br>
  financial situation, whatever it is. We use an innovative, simple and effective, which allows you to shop an insurance policy in the comfort of your home thanks in particular to our insurance quote forms online. Le Pont d'Oriole allows you to find the best price for:
</div>
<div class="abs tags">
  <span><i><svg width="6" height="8" viewBox="0 0 6 8"><path d="M1 1l4 3-4 3" stroke="#fff" stroke-width="1.5" fill="none"/></svg></i>Permanent life insurance - term life insurance</span>
  <span><i><svg width="6" height="8" viewBox="0 0 6 8"><path d="M1 1l4 3-4 3" stroke="#fff" stroke-width="1.5" fill="none"/></svg></i>Isability insurance - disability insurance</span>
  <span><i><svg width="6" height="8" viewBox="0 0 6 8"><path d="M1 1l4 3-4 3" stroke="#fff" stroke-width="1.5" fill="none"/></svg></i>Mortgage insurance - loans</span>
  <span><i><svg width="6" height="8" viewBox="0 0 6 8"><path d="M1 1l4 3-4 3" stroke="#fff" stroke-width="1.5" fill="none"/></svg></i>Critical illness insurance</span>
</div>

<article class="abs article" style="left:101px">
  <div class="photo" role="img" aria-label="Photo of hands sheltering a small house model" style="background:linear-gradient(135deg,#2d3e58,#6d7f96)"></div>
  <h4>Competent financial advisors Security</h4>
  <p>Team Le Pont d'Oriole offers an innovative service in the field of insurance. With our proven methods and our skill, you're guaranteed to find...</p>
  <span class="red-btn">READ MORE</span>
</article>
<article class="abs article" style="left:444px">
  <div class="photo" role="img" aria-label="Photo of a couple meeting an advisor at a table" style="background:linear-gradient(135deg,#e8e4dc,#b9aa96)"></div>
  <h4>The importance of not overpaying</h4>
  <p>Disbursing monthly or annually money for insurance is a considerable expense. Even if your payments do not think are high in the long run, money...</p>
  <span class="red-btn">READ MORE</span>
</article>
<article class="abs article" style="left:788px">
  <div class="photo" role="img" aria-label="Photo of a handshake over signed documents" style="background:linear-gradient(135deg,#f3f1ee,#c9b8a4)"></div>
  <h4>Insurance: ? How to find</h4>
  <p>Life insurance market premium may seem complex at first. Indeed, insurers offer a variety of products with different characteristics, and it is...</p>
  <span class="red-btn">READ MORE</span>
</article>

<!-- blog -->
<section class="abs blog"></section>
<h2 class="abs blog-title center-title" style="left:0">RECENT BLOG POST</h2>
<p class="abs blog-sub center-title" style="left:0">Sed ut perspiciatis unde omnis iste natus error sit voluptatem accusantium doloremque</p>
<span class="abs view-all">View All +</span>

<article class="abs post" style="left:98px">
  <div class="photo" role="img" aria-label="Photo of a business team" style="background:linear-gradient(135deg,#9aa7b8,#e5e8ec)"></div>
  <div class="body">
    <h5>Sed ut perspiciatis unde omnis error sit voluptatem accusantium tore</h5>
    <div class="date">POSTED MARCH 28, 2016</div>
    <p>Scientists may be able to predict who is more following a stroke by examining...</p>
  </div>
</article>
<article class="abs post" style="left:615px">
  <div class="photo" role="img" aria-label="Photo of a family outdoors" style="background:linear-gradient(135deg,#c7d9ea,#d9b8a0)"></div>
  <div class="body">
    <h5>Sed ut perspiciatis unde omnis error sit voluptatem accusantium tore</h5>
    <div class="date">POSTED MARCH 31, 2016</div>
    <p>Scientists may be able to predict who is more following a stroke by examining...</p>
  </div>
</article>

<!-- footer -->
<footer class="abs footer"></footer>
<div class="abs foot-col" style="left:98px">
  <h6>Menu</h6>
  <ul><li>HOME</li><li>PRODUCTS</li><li>SUBMISSIO</li><li>WHO ARE WE?</li><li>CONTACT US</li></ul>
</div>
<div class="abs foot-col" style="left:262px">
  <h6>Hours of operation</h6>
  <table class="hours">
    <tr><td>Monday</td><td>:</td><td>7am to 21hrs</td></tr>
    <tr><td>Tuesday</td><td>:</td><td>7am to 21hrs</td></tr>
    <tr><td>Wednesday</td><td>:</td><td>7am to 21hrs</td></tr>
    <tr><td>Thurs day</td><td>:</td><td>7am to 21hrs</td></tr>
    <tr><td>Friday</td><td>:</td><td>7am to 21hrs</td></tr>
    <tr class="sat"><td>Saturday</td><td>:</td><td>7am to 21hrs</td></tr>
  </table>
</div>
<div class="abs foot-col" style="left:508px">
  <h6>Our offices</h6>
  <div class="offices">
    <span>Montreal</span><span>Saguenay</span><span>Victoriaville</span>
    <span>Quebec</span><span>Goods</span><span>Amqui</span>
    <span>Sherbrooke</span><span>Chicoutimi</span><span>Wolf River</span>
    <span>Granby</span><span>Sept-iles</span><span>Chateauguay</span>
    <span>Beauce</span><span>Rouyn-Noranda</span><span>La Prairie</span>
    <span>three Rivères</span><span>Val D'Or</span><span></span>
  </div>
</div>
<div class="abs foot-col" style="left:886px">
  <h6>Contact us</h6>
  <div class="contact-line"><svg width="10" height="13" viewBox="0 0 10 13"><path d="M5 0a5 5 0 00-5 5c0 4 5 8 5 8s5-4 5-8a5 5 0 00-5-5z" fill="#d42a2a"/><circle cx="5" cy="5" r="2" fill="#fff"/></svg>48 Rue des Érables, La Prairie, QC, J5R 0A1</div>
  <div class="contact-line"><svg width="11" height="11" viewBox="0 0 24 24"><path fill="#d42a2a" d="M6.6 10.8a15 15 0 006.6 6.6l2.2-2.2c.3-.3.7-.4 1-.2 1.1.4 2.3.6 3.6.6.6 0 1 .4 1 1V20c0 .6-.4 1-1 1A17 17 0 013 4c0-.6.4-1 1-1h3.5c.6 0 1 .4 1 1 0 1.3.2 2.5.6 3.6.1.3 0 .7-.2 1z"/></svg>Toll free: <span style="color:var(--red)">1-855-555-0142</span></div>
  <div class="contact-line"><svg width="12" height="9" viewBox="0 0 24 18"><rect x="0" y="0" width="24" height="18" fill="#d42a2a"/><path d="M1 1l11 9 11-9" fill="none" stroke="#fff" stroke-width="2"/></svg>contact@lepontdoriole.ca</div>
  <div class="socials">
    <span style="background:#3b5a9a"></span><span style="background:#2aa3e0"></span><span style="background:#dd4b39"></span><span style="background:#0e76a8"></span><span style="background:#cb2027"></span>
  </div>
</div>
<div class="abs copyright">COPYRIGHTS©LEPONTDORIOLE.2016 | ALLRIGHTS RESERVED.</div>

</body>
</html>
```